Harborview Estates Business Card for Apartment Buildings

Create business cards for resident managers who run apartment buildings. The audience is the public who are searching for apartment rentals, and current residents who live at the apartment building. Key design element will be incorporating the company logo, however, the logo cannot dominate. The building name and manager name are more important than the logo. Current business card design leaves little room for copy, so we may need to reduce the size on the current card to allow for more space for copy.

Target Market(s)

Adults 18-65 years of age, who are looking for an apartment rental, plus current residents who live at our apartment buildings.

Industry/Entity Type

Property Management

Contact Information for Business Card

A major design element will be use of the company logo. Important property and manager contact information must be part of the design. The size of the logo will need to be reduced to make room for building and manager contact copy.

Font styles to use
Sans Serif

Colors
3176b5
000000
959595
ffffff

Requirements
Must have
• 1) Incorporate the company logo.
• 2) Use the company colors (dark blue, black/grey, over white).
• 3) FEATURE THE BUILDING NAME
• 4) FEATURE THE MANAGER NAME
• 5) The company name is less important than BUILDING and MANAGER
• 6) Manager contact information
• **SEE ATTACHED CREATIVE BRIEF**
Nice to have
• 1) Back of card logo watermark
• 2) Ability to write notes on back of carfd
Should not have
• Avoid letting the company logo dominate the card, the building name and manager are more important than the company logo.

```html
<!DOCTYPE html>
<html lang="en">
<head>
<meta charset="utf-8">
<title>Harborview Estates – Business Card</title>
<link href="https://fonts.googleapis.com/css2?family=Oswald:wght@500&family=Roboto:wght@400;500;700&display=swap" rel="stylesheet">
<style>
  :root {
    --blue: #215b8c;
    --ink: #1c1c1c;
    --grey: #959595;
    --card: #ffffff;
    --backdrop: #e9e9e9;
  }
  html, body {
    margin: 0;
    padding: 0;
    width: 1200px;
    height: 1054px;
    overflow: hidden;
    background: var(--backdrop);
  }
  .card {
    position: absolute;
    left: 100px;
    top: 227px;
    width: 1000px;
    height: 600px;
    background: var(--card);
    border: 1px solid #d6d6d6;
    box-shadow: 0 6px 24px rgba(0,0,0,0.08);
    font-family: "Roboto", Arial, sans-serif;
    color: var(--ink);
  }
  .manager-name {
    position: absolute;
    left: 76px;
    top: 86px;
    margin: 0;
    font-family: "Oswald", "Arial Narrow", sans-serif;
    font-weight: 500;
    font-size: 62px;
    line-height: 1;
    color: var(--blue);
    letter-spacing: 0.3px;
  }
  .manager-title {
    position: absolute;
    left: 76px;
    top: 160px;
    margin: 0;
    font-size: 34px;
    font-weight: 400;
  }
  .address {
    position: absolute;
    left: 76px;
    top: 315px;
    margin: 0;
    font-style: normal;
    font-size: 25px;
    line-height: 33px;
  }
  .contacts {
    position: absolute;
    left: 76px;
    top: 405px;
    margin: 0;
    padding: 0;
    list-style: none;
    font-size: 25px;
    line-height: 33px;
  }
  .contacts li {
    display: flex;
    align-items: center;
    height: 33px;
  }
  .contacts svg {
    width: 22px;
    height: 22px;
    margin-right: 22px;
    flex: none;
  }
  .domain { color: var(--blue); }
  .building-mark {
    position: absolute;
    right: 80px;
    bottom: 62px;
    display: flex;
    align-items: center;
    gap: 18px;
  }
  .building-mark .square {
    width: 34px;
    height: 34px;
    background: var(--blue);
    flex: none;
  }
  .building-name {
    margin: 0;
    font-size: 40px;
    font-weight: 700;
    line-height: 44px;
    color: var(--blue);
  }
</style>
</head>
<body>
  <section class="card">
    <h1 class="manager-name">DANA WHITFIELD</h1>
    <p class="manager-title">Property Manager</p>

    <address class="address">
      2750 Larkspur Valley Road<br>
      #B210 San Diego, CA 92108
    </address>

    <ul class="contacts">
      <li>
        <svg viewBox="0 0 24 24" aria-label="Phone"><circle cx="12" cy="12" r="10" fill="none" stroke="#215b8c" stroke-width="2"/><path d="M8.5 7.5c.6-.6 1.3-.5 1.6.1l.8 1.6c.2.5 0 .9-.3 1.2l-.5.5c.6 1.3 1.6 2.3 2.9 2.9l.5-.5c.3-.3.8-.5 1.2-.3l1.6.8c.6.3.7 1 .1 1.6-1.1 1.1-2.6 1.2-4.4.1-1.5-.9-2.8-2.2-3.7-3.7-1.1-1.8-1-3.3.2-4.3z" fill="#215b8c"/></svg>
        <span>555-214-7390</span>
      </li>
      <li>
        <svg viewBox="0 0 24 24" aria-label="Fax"><rect x="6" y="2" width="12" height="6" fill="#215b8c"/><rect x="2" y="9" width="20" height="9" rx="2" fill="#215b8c"/><rect x="6" y="14" width="12" height="8" fill="#fff" stroke="#215b8c" stroke-width="2"/></svg>
        <span>555-214-7391</span>
      </li>
      <li>
        <svg viewBox="0 0 24 24" aria-label="Email"><rect x="2" y="5" width="20" height="14" fill="none" stroke="#215b8c" stroke-width="2"/><path d="M2 5l10 8 10-8" fill="none" stroke="#215b8c" stroke-width="2"/></svg>
        <span>dana@harborviewestates.us</span>
      </li>
      <li>
        <svg viewBox="0 0 24 24" aria-label="Website"><circle cx="12" cy="12" r="10" fill="#215b8c"/><path d="M2 12h20M12 2c-3 3-3 17 0 20M12 2c3 3 3 17 0 20M4 7h16M4 17h16" fill="none" stroke="#fff" stroke-width="1.3"/></svg>
        <span>www.<span class="domain">harborviewestates</span>.us</span>
      </li>
    </ul>

    <div class="building-mark">
      <span class="square"></span>
      <p class="building-name">Harborview<br>Estates</p>
    </div>
  </section>
</body>
</html>
```